Mortgage Specialist Wordpress Build

I have a current WordPress site but I would like a whole new site built using the same domain. I've included a site for reference in my outline. The main focus of the website is to educate and capture leads.
I would like my blogs to stay for SEO already earned. Please see work requested attached.
Updates
Project Deadline Extended Reason: I am extending the deadline because I didn't realize this was a design only and I need the website coded as well. I've purchased the add-on. This is my first time using Pixel Harbor so please bare with me. I have additional Wordpress sites I want to have built too. Thanks, Colin Added Tuesday, April 18, 2017
Target Market(s)
Home Buyers, Home owners looking to refinance or renew their mortgages
Industry/Entity Type
Mortgage
Coding
Coded - Design and coding required
Font styles to use
Look and feel
Each slider illustrates characteristics of the customer's brand and the style your logo design should communicate.

```html
<!DOCTYPE html>
<html lang="en">
<head>
<meta charset="utf-8">
<title>Harborline Lending – Mortgage Specialist</title>
<link rel="stylesheet" href="https://fonts.googleapis.com/css2?family=Open+Sans:wght@400;600;700&display=swap">
<style>
  :root {
    --navy: #003b80;
    --navy-text: #1e4b8a;
    --gold: #efc320;
    --gold-soft: #f8e7a3;
    --cream: #f7e6a6;
    --band: #ebebee;
    --ink: #2f2f2f;
    --muted: #5a5a5a;
    --white: #ffffff;
    --line: #e2e2e2;
  }
  * { box-sizing: border-box; margin: 0; padding: 0; }
  html, body { width: 1200px; height: 2329px; overflow: hidden; }
  body { position: relative; font-family: "Open Sans", Arial, sans-serif; color: var(--ink); background: var(--white); }
  .abs { position: absolute; }

  /* Header */
  .site-header { position: absolute; left: 0; top: 0; width: 1200px; height: 106px; background: var(--navy); }
  .brand { position: absolute; left: 132px; top: 28px; display: flex; align-items: center; gap: 12px; color: var(--white); font-size: 22px; font-weight: 600; letter-spacing: 0.5px; }
  .brand-mark { width: 26px; height: 26px; background: var(--gold); }
  .main-nav { position: absolute; top: 43px; left: 560px; height: 25px; }
  .main-nav a { position: absolute; top: 0; height: 25px; line-height: 25px; font-size: 12px; font-weight: 600; color: var(--white); text-decoration: none; white-space: nowrap; }
  .main-nav .current { left: 0; width: 61px; background: var(--gold); color: var(--navy); text-align: center; }
  .search-box { position: absolute; left: 958px; top: 37px; width: 108px; height: 33px; border: 1px solid rgba(255,255,255,0.45); color: var(--white); font-size: 9px; line-height: 31px; padding-left: 14px; }
  .search-box svg { position: absolute; right: 10px; top: 11px; }

  /* Hero */
  .hero { position: absolute; left: 0; top: 106px; width: 1200px; height: 572px; background: linear-gradient(100deg, #6f6e6b 0%, #8a8784 40%, #77706a 70%, #9c9894 100%); }
  .hero::after { content: ""; position: absolute; inset: 0; background: rgba(40,40,40,0.35); }
  .hero-content { position: absolute; inset: 0; z-index: 1; }
  .play { position: absolute; left: 551px; top: 126px; }
  .hero-title { position: absolute; left: 0; width: 1200px; top: 258px; text-align: center; color: var(--white); font-size: 40px; font-weight: 600; }
  .hero-sub { position: absolute; left: 0; width: 1200px; top: 318px; text-align: center; color: var(--white); font-size: 16px; }
  .btn { position: absolute; display: block; text-align: center; font-weight: 600; color: #3a3a3a; text-decoration: none; }
  .hero .btn { top: 366px; width: 248px; height: 63px; line-height: 63px; font-size: 22px; }
  .btn-primary { background: var(--gold); }
  .btn-secondary { background: var(--gold-soft); }
  .scroll-cue { position: absolute; left: 587px; top: 486px; }

  /* Partners */
  .partners { position: absolute; left: 0; top: 678px; width: 1200px; height: 134px; background: var(--band); }
  .partners .arrow { position: absolute; top: 52px; }
  .partner-badge { position: absolute; background: #c9c9cf; }

  /* Services */
  .section-title { position: absolute; left: 0; width: 1200px; text-align: center; }
  .help-title { top: 872px; font-size: 31px; color: var(--navy-text); }
  .service-card { position: absolute; top: 984px; width: 284px; height: 275px; background: var(--cream); text-align: center; }
  .service-card::after { content: ""; position: absolute; left: 131px; bottom: 0; border-left: 11px solid transparent; border-right: 11px solid transparent; border-bottom: 11px solid var(--white); }
  .service-card svg { position: absolute; left: 118px; top: 34px; }
  .service-name { position: absolute; left: 0; width: 284px; top: 112px; font-size: 27px; color: #333; }
  .service-card .btn { left: 78px; top: 188px; width: 128px; height: 42px; line-height: 42px; font-size: 14px; font-weight: 400; background: var(--gold); }

  /* Ask */
  .ask-band { position: absolute; left: 0; top: 1350px; width: 1200px; height: 354px; background: linear-gradient(90deg, #5e564e 0%, #7a6d62 45%, #6e655d 70%, #847c74 100%); }
  .ask-title { top: 1454px; font-size: 34px; font-weight: 600; color: var(--white); }
  .ask-band + .ask-title + .btn, .ask-btn { left: 535px; top: 1541px; width: 129px; height: 59px; line-height: 59px; font-size: 23px; background: var(--gold); }

  /* Brokers */
  .broker-info { position: absolute; top: 1704px; width: 303px; height: 390px; background: var(--cream); text-align: center; }
  .broker-name { position: absolute; left: 0; width: 303px; top: 52px; font-size: 17px; line-height: 26px; color: #333; }
  .broker-bio { position: absolute; left: 60px; width: 183px; top: 136px; font-size: 12px; line-height: 20.5px; color: var(--muted); }
  .social-row { position: absolute; display: flex; gap: 6px; }
  .social-row span { width: 19px; height: 19px; background: var(--navy); }
  .broker-photo { position: absolute; top: 1704px; width: 303px; height: 390px; }

  /* Footer */
  .footer-brand { position: absolute; left: 132px; top: 2150px; display: flex; align-items: center; gap: 12px; font-size: 22px; font-weight: 600; color: #222; }
  .footer-brand span.sq { width: 26px; height: 26px; background: #222; }
  .anniversary { position: absolute; left: 543px; top: 2130px; width: 106px; height: 62px; border-radius: 31px; background: #d6dbe6; }
  .follow { position: absolute; left: 912px; top: 2136px; font-size: 10px; color: #444; }
  .footer-rule { position: absolute; left: 0; top: 2236px; width: 1200px; height: 1px; background: var(--line); }
  .contact-line { position: absolute; top: 2273px; font-size: 11px; color: #444; display: flex; align-items: center; gap: 10px; white-space: nowrap; }
  .copyright { position: absolute; right: 135px; top: 2273px; font-size: 11px; color: #444; }
</style>
</head>
<body>

<header class="site-header">
  <div class="brand"><span class="brand-mark"></span>Harborline Lending</div>
  <nav class="main-nav">
    <a class="current" href="#">HOME</a>
    <a href="#" style="left:104px">ABOUT</a>
    <a href="#" style="left:205px">BLOG</a>
    <a href="#" style="left:294px">CONTACT</a>
  </nav>
  <div class="search-box">SEARCH
    <svg width="10" height="10" viewBox="0 0 10 10"><circle cx="4" cy="4" r="3" fill="none" stroke="#fff" stroke-width="1.4"/><line x1="6.2" y1="6.2" x2="9" y2="9" stroke="#fff" stroke-width="1.4"/></svg>
  </div>
</header>

<section class="hero" role="img" aria-label="Photo of a mortgage broker meeting a young couple at an office table">
  <div class="hero-content">
    <svg class="play" width="94" height="94" viewBox="0 0 94 94"><circle cx="47" cy="47" r="42" fill="none" stroke="rgba(255,255,255,0.85)" stroke-width="8"/><polygon points="37,28 37,66 67,47" fill="rgba(255,255,255,0.85)"/></svg>
    <h1 class="hero-title">Become a home buying</h1>
    <p class="hero-sub">Purchasing a home can be a daunting task as the market continues to sizzle</p>
    <a class="btn btn-primary" href="#" style="left:337px">Get Hooked Up</a>
    <a class="btn btn-secondary" href="#" style="left:616px">I’m a client</a>
    <svg class="scroll-cue" width="26" height="22" viewBox="0 0 26 22"><polyline points="2,2 13,10 24,2" fill="none" stroke="#fff" stroke-width="3"/><polyline points="2,11 13,19 24,11" fill="none" stroke="#fff" stroke-width="3"/></svg>
  </div>
</section>

<section class="partners" aria-label="Lending partners">
  <svg class="arrow" style="left:132px" width="16" height="30" viewBox="0 0 16 30"><polyline points="14,2 2,15 14,28" fill="none" stroke="#9a9aa2" stroke-width="2.5"/></svg>
  <div class="partner-badge" style="left:258px;top:44px;width:86px;height:46px;"></div>
  <div class="partner-badge" style="left:388px;top:36px;width:62px;height:62px;"></div>
  <div class="partner-badge" style="left:496px;top:34px;width:84px;height:66px;"></div>
  <div class="partner-badge" style="left:662px;top:56px;width:86px;height:22px;"></div>
  <div class="partner-badge" style="left:778px;top:36px;width:78px;height:60px;"></div>
  <div class="partner-badge" style="left:908px;top:32px;width:62px;height:62px;"></div>
  <svg class="arrow" style="left:1048px" width="16" height="30" viewBox="0 0 16 30"><polyline points="2,2 14,15 2,28" fill="none" stroke="#9a9aa2" stroke-width="2.5"/></svg>
</section>

<h2 class="section-title help-title">I need help with</h2>

<article class="service-card" style="left:132px">
  <svg width="48" height="44" viewBox="0 0 48 44"><path d="M4 16h40l-5 24H9z" fill="none" stroke="#333" stroke-width="2"/><path d="M14 16l8-12M34 16l-8-12" stroke="#333" stroke-width="2" fill="none"/><path d="M2 16h44" stroke="#333" stroke-width="2"/><path d="M16 24v9M21 22v11M26 26v7M31 24v9" stroke="#333" stroke-width="2"/></svg>
  <h3 class="service-name">Purchase</h3>
  <a class="btn" href="#">CLICK HERE</a>
</article>
<article class="service-card" style="left:458px">
  <svg width="48" height="48" viewBox="0 0 48 48"><path d="M40 14A19 19 0 1 0 43 27" fill="none" stroke="#333" stroke-width="2"/><polyline points="34,13 41,14 42,7" fill="none" stroke="#333" stroke-width="2"/><text x="24" y="31" text-anchor="middle" font-family="Open Sans, sans-serif" font-size="19" fill="#333">$</text></svg>
  <h3 class="service-name">Refinance</h3>
  <a class="btn" href="#">CLICK HERE</a>
</article>
<article class="service-card" style="left:782px">
  <svg width="48" height="48" viewBox="0 0 48 48"><path d="M8 22A16 16 0 0 1 38 14" fill="none" stroke="#333" stroke-width="2"/><polyline points="39,6 39,15 30,15" fill="none" stroke="#333" stroke-width="2"/><path d="M40 26A16 16 0 0 1 10 34" fill="none" stroke="#333" stroke-width="2"/><polyline points="9,42 9,33 18,33" fill="none" stroke="#333" stroke-width="2"/></svg>
  <h3 class="service-name">Renew</h3>
  <a class="btn" href="#">CLICK HERE</a>
</article>

<section class="ask-band" role="img" aria-label="Photo of a family carrying moving boxes into a new home"></section>
<h2 class="section-title ask-title">Mortgage or Real Estate Questions?</h2>
<a class="btn ask-btn" href="#">ASK</a>

<div class="broker-info" style="left:0">
  <h3 class="broker-name">Northbay<br>Mortgage Broker</h3>
  <p class="broker-bio">Purchasing a home, refinancing a mortgage and renewing a mortgage have one thing in common: they can represent an exciting time in an individual’s life but they can also be complex.</p>
  <div class="social-row" style="left:86px;top:326px"><span></span><span></span><span></span><span></span><span></span></div>
</div>
<div class="broker-photo" style="left:303px;background:linear-gradient(180deg,#3c3c3e,#2a2a2c);" role="img" aria-label="Portrait photo of the Northbay mortgage broker"></div>
<div class="broker-info" style="left:606px">
  <h3 class="broker-name">Martin Alvarez</h3>
  <p class="broker-bio">Purchasing a home, refinancing a mortgage and renewing a mortgage have one thing in common: they can represent an exciting time in an individual’s life but they can also be complex.</p>
  <div class="social-row" style="left:86px;top:326px"><span></span><span></span><span></span><span></span><span></span></div>
</div>
<div class="broker-photo" style="left:909px;background:linear-gradient(180deg,#e6e6e4,#bdbcb8);" role="img" aria-label="Portrait photo of broker Martin Alvarez"></div>

<footer>
  <div class="footer-brand"><span class="sq"></span>Harborline Lending</div>
  <div class="anniversary" aria-label="Anniversary badge"></div>
  <div class="follow">FOLLOW US ON</div>
  <div class="social-row" style="left:912px;top:2166px"><span style="width:24px;height:24px"></span><span style="width:24px;height:24px"></span><span style="width:24px;height:24px"></span><span style="width:24px;height:24px"></span><span style="width:24px;height:24px"></span></div>
  <div class="footer-rule"></div>
  <div class="contact-line" style="left:133px">
    <svg width="8" height="11" viewBox="0 0 8 11"><path d="M4 0a4 4 0 0 1 4 4c0 3-4 7-4 7S0 7 0 4a4 4 0 0 1 4-4z" fill="#333"/><circle cx="4" cy="4" r="1.5" fill="#fff"/></svg>
    140 Quayside Rd. Northbay, BC V0X 1A0
  </div>
  <div class="contact-line" style="left:420px">
    <svg width="11" height="11" viewBox="0 0 11 11"><path d="M2 0l2 3-1 1.5a6 6 0 0 0 3.5 3.5L8 7l3 2-1.5 2C5 11 0 6 0 1.5z" fill="#333"/></svg>
    555.010.2244
  </div>
  <div class="contact-line" style="left:545px">
    <svg width="12" height="9" viewBox="0 0 12 9"><rect width="12" height="9" fill="#333"/><polyline points="0,0 6,5 12,0" fill="none" stroke="#fff" stroke-width="1"/></svg>
    colin@harborlinemortgage.example
  </div>
  <div class="copyright">Copyrights @ 2017 All Rights Reserved</div>
</footer>

</body>
</html>
```